HarborQuote - Webstartup looking for some style

HarborQuote is a cloud based web application that allows construction sub-contractors to create and manage bids. Generally, these contractors will contact subcontractors to have them do specific parts of a larger construction project. This would be used by various subcontractors including woodwork (cabinetry), electricians, masons, etc...

Nearly all competitors are clients applications that have to be installed on the computer and are very expensive. This is a much lower cost alternative.

The business is just beginning and we want people to view us as a fresh alternative to companies that have been around for a long time and are starting to look a little dated.

We would like our logo included on the card (see attached). We have been using the circular 'hq' emblem seperately from the complete logo in various areas of the website. We lean towards a professional and clean look, with a tendancy more towards modern.

We want to differentiate ourselves from our competition which tend to be dated, complicated and less graphical.

(We are currently designing our public website as well - but don't have any designs yet)

Industry/Entity Type

Construction

Requirements
Must have
• Circular 'hq' emblem from logo. Probably entire logo, but not necessarily.

Should have reference to website: www.harborquote-example.com

The Url should be all lowercase (www.harborquote-example.com)
Should not have
• we do not want to list a phone number or email address on the cards. we want people to go to the actual website. we haven't decided if we want names printed on the business cards.

```html
<!DOCTYPE html>
<html lang="en">
<head>
<meta charset="utf-8">
<title>HarborQuote Business Cards</title>
<link rel="stylesheet" href="https://fonts.googleapis.com/css2?family=Josefin+Sans:wght@300;400&family=Roboto+Condensed:wght@700&family=Varela+Round&display=swap">
<style>
  :root {
    --stage: #1a6aa8;
    --blue: #1f8ad0;
    --blue-light: #3ea0dc;
    --orange: #f39a24;
    --white: #ffffff;
    --paper: #f3f3f3;
    --ink: #2b2b2b;
  }
  * { margin: 0; padding: 0; box-sizing: border-box; }
  html, body { width: 1200px; height: 1200px; overflow: hidden; }
  body {
    background: var(--stage);
    position: relative;
    font-family: "Josefin Sans", sans-serif;
  }
  .card {
    position: absolute;
    left: 180px;
    width: 840px;
    height: 480px;
    overflow: hidden;
  }
  .card--front { top: 90px; background: var(--blue); }
  .card--back { top: 630px; background: var(--orange); }

  /* front card */
  .front__top-band {
    position: absolute; left: 0; top: 0; width: 100%; height: 110px;
    background: var(--blue-light);
  }
  .front__orange-column {
    position: absolute; right: 0; top: 0; width: 380px; height: 100%;
    background: var(--orange);
  }
  .front__white-band {
    position: absolute; left: 0; top: 110px; width: 100%; height: 250px;
    background: linear-gradient(180deg, var(--white), var(--paper));
  }
  .front__logo {
    position: absolute; left: 150px; top: 150px;
    display: flex; align-items: center; gap: 20px;
  }
  .brand-dot {
    width: 96px; height: 96px; border-radius: 50%;
    background: var(--blue);
    flex: none;
  }
  .front__wordmark { display: flex; flex-direction: column; }
  .front__name {
    font-weight: 400;
    font-size: 70px; line-height: 1; color: var(--blue);
  }
  .tagline {
    font-family: "Roboto Condensed", sans-serif; font-weight: 700;
    font-size: 19px; color: var(--ink); margin-top: 8px;
  }
  .front__url {
    position: absolute; left: 0; width: 100%; top: 292px;
    text-align: center;
    font-family: "Varela Round", sans-serif; font-size: 36px;
    letter-spacing: 3px; color: var(--blue);
  }

  /* back card */
  .back__blue-panel {
    position: absolute; left: 0; top: 0; width: 260px; height: 100%;
    background: var(--blue);
  }
  .back__glow {
    position: absolute; right: 0; top: 0; width: 580px; height: 100%;
    background: linear-gradient(135deg, rgba(255,255,255,0.22), rgba(255,255,255,0) 60%);
  }
  .back__ring {
    position: absolute; left: 90px; top: 50px;
    width: 230px; height: 230px; border-radius: 50%;
    border: 28px solid var(--white);
  }
  .back__signature {
    position: absolute; right: 50px; bottom: 40px; text-align: right;
    color: var(--white);
  }
  .back__name {
    font-weight: 300;
    font-size: 66px; line-height: 1;
  }
  .back__signature .tagline { color: var(--white); font-size: 17px; margin-top: 6px; }
  .back__url {
    font-family: "Varela Round", sans-serif; font-size: 30px;
    letter-spacing: 2px; margin-top: 10px;
  }
</style>
</head>
<body>
  <section class="card card--front" aria-label="Business card front">
    <div class="front__top-band"></div>
    <div class="front__orange-column"></div>
    <div class="front__white-band"></div>
    <div class="front__logo">
      <div class="brand-dot"></div>
      <div class="front__wordmark">
        <span class="front__name">HarborQuote</span>
        <span class="tagline">Streamlining Subcontractor Bidding</span>
      </div>
    </div>
    <p class="front__url">www.harborquote-example.com</p>
  </section>

  <section class="card card--back" aria-label="Business card back">
    <div class="back__blue-panel"></div>
    <div class="back__glow"></div>
    <div class="back__ring"></div>
    <div class="back__signature">
      <p class="back__name">HarborQuote</p>
      <p class="tagline">Streamlining Subcontractor Bidding</p>
      <p class="back__url">www.harborquote-example.com</p>
    </div>
  </section>
</body>
</html>
```